SkyvornQ Business Cards and Stationary Design

Need a design for our business cards and stationary. I want to carry on the theme of the logo. I want the business cards to have a design on the back. I would like the business cards and the stationary to carry the same theme, design scheme, and branding

Target Market(s)

Airlines and Maintenance Facilities

Industry/Entity Type

Aviation

Contact Information for Business Card

Name
Position Title
Address: 4827 Trellis Hollow Road, Fort Pierce, Florida, 34951
Office Number
Mobile Number
Email
Website

Font styles to use
Serif
Sans Serif

Colors

Designer to choose colors to be used in the design.

```html
<!DOCTYPE html>
<html lang="en">
<head>
<meta charset="utf-8">
<title>SkyvornQ Business Cards</title>
<link href="https://fonts.googleapis.com/css2?family=Open+Sans:wght@400;600;700&family=Montserrat:wght@700&display=swap" rel="stylesheet">
<style>
  :root {
    --navy: #0e2a5e;
    --blue-light: #1d86cc;
    --blue-deep: #0b3d88;
    --card-white: #ffffff;
    --backdrop: #e7e9ee;
    --ink-grey: #3a3f4a;
  }
  * { box-sizing: border-box; margin: 0; padding: 0; }
  html, body { width: 1200px; height: 872px; overflow: hidden; }
  body {
    background: var(--backdrop);
    font-family: "Open Sans", Arial, sans-serif;
    position: relative;
  }
  .card {
    position: absolute;
    left: 290px;
    width: 620px;
    height: 354px;
    background: var(--card-white);
    box-shadow: 0 6px 18px rgba(0,0,0,0.18);
    overflow: hidden;
  }
  .card-back { top: 40px; }
  .card-front { top: 476px; }

  .brand {
    display: flex;
    align-items: center;
    justify-content: center;
    gap: 16px;
  }
  .brand-dot {
    width: 44px; height: 44px;
    border-radius: 50%;
    background: var(--blue-light);
  }
  .brand-name {
    font-family: "Montserrat", Arial, sans-serif;
    font-weight: 700;
    color: var(--navy);
    letter-spacing: 6px;
    font-size: 40px;
  }

  .card-back .brand { margin-top: 118px; }
  .back-web {
    text-align: center;
    margin-top: 22px;
    font-size: 16px;
    letter-spacing: 5px;
    color: var(--ink-grey);
  }

  .card-front .brand { margin-top: 52px; }
  .holder {
    text-align: center;
    margin-top: 36px;
    font-size: 20px;
    color: var(--navy);
  }
  .holder-name { font-weight: 700; }
  .holder-title { font-weight: 400; color: var(--ink-grey); }

  .rule {
    position: absolute;
    left: 0; right: 0;
    top: 222px;
    height: 2px;
    background: var(--navy);
  }
  .contact-band {
    position: absolute;
    left: 0; right: 0;
    top: 230px; bottom: 0;
    background: linear-gradient(180deg, var(--blue-light), var(--blue-deep));
    color: #fff;
    font-size: 14px;
    padding-top: 14px;
  }
  .contact-row {
    display: flex;
    justify-content: center;
    gap: 26px;
    line-height: 32px;
  }
  .contact-item { display: flex; align-items: center; gap: 6px; }
  .contact-item svg { width: 15px; height: 15px; fill: none; stroke: #fff; stroke-width: 1.6; }
</style>
</head>
<body>

<section class="card card-back">
  <div class="brand">
    <span class="brand-dot"></span>
    <span class="brand-name">SKYVORNQ</span>
  </div>
  <p class="back-web">www.skyvornq.com</p>
</section>

<section class="card card-front">
  <div class="brand">
    <span class="brand-dot"></span>
    <span class="brand-name">SKYVORNQ</span>
  </div>
  <p class="holder"><span class="holder-name">DORIAN VELCOTT</span><span class="holder-title">, PRESIDENT</span></p>
  <div class="rule"></div>
  <div class="contact-band">
    <div class="contact-row">
      <span class="contact-item">
        <svg viewBox="0 0 16 16"><circle cx="8" cy="8" r="7"/><path d="M5.5 4.5l1.5 1.5-1 1a5 5 0 0 0 3 3l1-1 1.5 1.5-1 1c-3 0-6-3-6-6z"/></svg>
        012-555-0147
      </span>
      <span class="contact-item">
        <svg viewBox="0 0 16 16"><rect x="4.5" y="1.5" width="7" height="13" rx="1.5"/><path d="M7 12.2h2"/></svg>
        012-555-0182
      </span>
    </div>
    <div class="contact-row">
      <span class="contact-item">
        <svg viewBox="0 0 16 16"><circle cx="8" cy="8" r="7"/><rect x="4.5" y="5.5" width="7" height="5"/><path d="M4.5 5.5l3.5 3 3.5-3"/></svg>
        info@skyvornq.com
      </span>
      <span class="contact-item">
        <svg viewBox="0 0 16 16"><circle cx="8" cy="8" r="7"/><ellipse cx="8" cy="8" rx="3" ry="7"/><path d="M1 8h14"/></svg>
        www.skyvornq.com
      </span>
    </div>
    <div class="contact-row">
      <span class="contact-item">
        <svg viewBox="0 0 16 16"><path d="M8 15s-5-5-5-8.5a5 5 0 0 1 10 0C13 10 8 15 8 15z"/><circle cx="8" cy="6.5" r="1.8"/></svg>
        4827 Trellis Hollow Road, Fort Pierce, Florida, 34951
      </span>
    </div>
  </div>
</section>

</body>
</html>
```